Occasions chocolate packaging

We are looking for 7 packaging designs for bars of chocolate.

Each design needs to be different and we’re not looking for a consistent brand or branding message across the designs. Inspiration should come from gift/occasion cards. Fun, simple, bold, vibrant colours and eye catching, i.e. not vintage or just text.

The front of the packaging should have the main message on and is free of any branding. You don’t need to design the back, just simply allow the main background colour or design pattern to continue around.

These are the different designs we are after, I’ve added in some text for each to give you some guidance but feel free to play around with the message if it suits the design better.

1) Mum
‘The best mum’, ‘Best mum in the World’, ‘Number 1 Mum’

2) Dad
‘The Best Dad’, ‘Best Dad Ever’, ‘Number 1 Dad’, ‘You’re my hero Dad’

3) Husband
‘Best Husband in the World’, ‘Husband I Love You’, ‘Darling Husband’

4) Wife
‘Best Wife in the World’, ‘For my Wonderful Wife’, ‘My Beautiful Wife’

5) Congratulations
Simple one, just Congratulations

6) Thinking of you
Try and keep this neutral as it could be used for happy and sad situations.

7) Thank you
Keep this gender neutral.

Sides:
The sides need to have the following text:

FINE BELGIAN DARK CHOCOLATE
infused with Orange

Back:
The main colour of the front should continue all the way around, we will place a box with the contents and bar code on here ourselves so no need to do anything.

Dimensions:
Attached in the document, front of package is 85mm by 190mm.

The packaging is made from folded card, the first blank part is for gluing the back on to.

Reason: I'm extending the deadline as I've only received 1 design so far which has followed the brief. Although I do like it, I would like to see at least some competition...

```html
<!DOCTYPE html>
<html lang="en">
<head>
<meta charset="UTF-8">
<title>Best Wife in the World – Chocolate Bar Wrapper</title>
<link rel="stylesheet" href="https://fonts.googleapis.com/css2?family=Oswald:wght@600;700&family=Raleway:wght@500;600&display=swap">
<style>
  :root {
    --backdrop: #e8e9eb;
    --wrap-purple: #5a2cc4;
    --wrap-purple-deep: #4a21a6;
    --wrap-purple-light: #6a3ad6;
    --heart-pink: #f4a9c8;
    --ink-white: #ffffff;
    --side-text: #efe9ff;
  }
  * { box-sizing: border-box; margin: 0; padding: 0; }
  html, body {
    width: 1200px;
    height: 960px;
    overflow: hidden;
    background: var(--backdrop);
  }
  .wrapper-layout {
    position: absolute;
    left: 385px;
    top: 50px;
    width: 430px;
    height: 860px;
    display: flex;
  }
  .side-panel {
    width: 45px;
    height: 100%;
    background: linear-gradient(180deg, var(--wrap-purple-deep), var(--wrap-purple));
    position: relative;
    overflow: hidden;
  }
  .side-label {
    position: absolute;
    left: 50%;
    top: 50%;
    width: 860px;
    transform: translate(-50%, -50%) rotate(-90deg);
    display: flex;
    justify-content: center;
    gap: 22px;
    color: var(--side-text);
    font-family: "Raleway", sans-serif;
    font-size: 19px;
    white-space: nowrap;
  }
  .side-label .product-name {
    font-weight: 600;
    letter-spacing: 3px;
    text-transform: uppercase;
  }
  .side-label .flavour {
    font-weight: 500;
    letter-spacing: 2px;
  }
  .front-panel {
    width: 385px;
    height: 100%;
    position: relative;
    overflow: hidden;
    background:
      radial-gradient(circle at 30% 40%, rgba(255,255,255,0.10) 0, rgba(255,255,255,0) 35%),
      radial-gradient(circle at 80% 75%, rgba(255,255,255,0.08) 0, rgba(255,255,255,0) 30%),
      linear-gradient(160deg, var(--wrap-purple-light) 0%, var(--wrap-purple) 45%, var(--wrap-purple-deep) 100%);
  }
  .love-heart {
    position: absolute;
    left: 112px;
    top: 25px;
    width: 220px;
    height: 205px;
  }
  .love-heart path { fill: var(--heart-pink); }
  .couple-artwork {
    position: absolute;
    left: 70px;
    top: 60px;
    width: 200px;
    height: 440px;
    border-radius: 60px 60px 30px 30px;
    background: linear-gradient(180deg, rgba(255,255,255,0.92) 0%, rgba(255,255,255,0.85) 60%, rgba(255,255,255,0.7) 100%);
  }
  .message {
    position: absolute;
    left: 0;
    right: 0;
    top: 505px;
    display: flex;
    flex-direction: column;
    align-items: center;
    color: var(--ink-white);
    text-align: center;
    padding-left: 20px;
  }
  .message-main {
    font-family: "Oswald", sans-serif;
    font-weight: 700;
    font-size: 116px;
    line-height: 1.0;
    letter-spacing: -2px;
    text-transform: uppercase;
  }
  .message-sub {
    font-family: "Oswald", sans-serif;
    font-weight: 600;
    font-size: 40px;
    line-height: 1.1;
    letter-spacing: -1.5px;
    text-transform: uppercase;
    margin-top: -2px;
  }
  .dedication {
    font-family: "Raleway", sans-serif;
    font-weight: 600;
    font-size: 18px;
    letter-spacing: 3px;
    text-transform: uppercase;
    margin-top: 10px;
    margin-left: -20px;
  }
</style>
</head>
<body>
  <div class="wrapper-layout">
    <section class="side-panel">
      <p class="side-label">
        <span class="product-name">Fine Belgian Dark Chocolate</span>
        <span class="flavour">infused with Orange</span>
      </p>
    </section>
    <section class="front-panel">
      <svg class="love-heart" viewBox="0 0 100 90" aria-hidden="true">
        <path d="M50 88 C20 65 0 48 0 26 C0 10 12 0 26 0 C38 0 46 8 50 16 C54 8 62 0 74 0 C88 0 100 10 100 26 C100 48 80 65 50 88Z"/>
      </svg>
      <div class="couple-artwork" role="img" aria-label="White silhouette of a man lifting a woman into the air in front of the pink heart"></div>
      <div class="message">
        <h1 class="message-main">Best<br>Wife</h1>
        <p class="message-sub">In the World</p>
        <p class="dedication">For my wonderful wife</p>
      </div>
    </section>
  </div>
</body>
</html>
```